K & R Acre Works. Business card design

We need a business card designed for a new business. We have a bulldozer and tractor service. We clear land and make wildlife food plots. We provide disking, bush hogging, and site prep services.
I have attached an image of a business card that I like and would like my business cards to look similar.

Target Market(s)

anyone needing bulldozer and/or tractor services

Industry/Entity Type

Business

Contact Information for Business Card

K & R Acre Works, Operated by 7-T-Ranch
Wade Colton
601-472-3358
wcr4817@fieldmail-example.com

Font styles to use
Sans Serif

Colors

Designer to choose colors to be used in the design.

Requirements
Must have
• image of tractor and bulldozer
• Land Clearing
• Wildlife food plots
• Bush Hogging
• Disking
• Site prep
Nice to have
• i have included a image of a business card that i like. I would like mine to be similar.

```html
<!DOCTYPE html>
<html lang="en">
<head>
<meta charset="utf-8">
<title>K &amp; R Acre Works – Business Card</title>
<link rel="stylesheet" href="https://fonts.googleapis.com/css2?family=Roboto+Condensed:wght@400;700&family=Noto+Sans:wght@400&display=swap">
<style>
  :root {
    --backdrop: #2b2b2b;
    --card-paper: #f2f2f0;
    --edge-brown: #7a4c12;
    --brand-brown: #7a4a12;
    --olive: #8e8a2c;
    --title-brown: #6b3a0e;
    --body-grey: #454545;
    --icon-olive: #8e8a2c;
    --photo-dozer-top: #8fa277;
    --photo-dozer-bottom: #6f6453;
    --photo-tractor-top: #5f8a3e;
    --photo-tractor-bottom: #a79a62;
  }
  * { margin: 0; padding: 0; box-sizing: border-box; }
  html, body {
    width: 1200px; height: 960px; overflow: hidden;
    background: var(--backdrop);
  }
  .card {
    position: absolute; left: 300px; top: 309px;
    width: 600px; height: 343px;
    background: var(--card-paper);
    box-shadow: 0 4px 10px rgba(0,0,0,.5);
    overflow: hidden;
  }
  .card__edge {
    position: absolute; left: 0; top: 0; width: 17px; height: 100%;
    background: var(--edge-brown);
  }
  .card__info {
    position: absolute; left: 55px; top: 0; width: 285px; height: 100%;
    font-family: "Noto Sans", sans-serif; color: var(--body-grey);
  }
  .brand {
    position: absolute; top: 40px; left: 0;
    display: flex; align-items: center; gap: 7px;
  }
  .brand__square { width: 14px; height: 14px; background: var(--brand-brown); }
  .brand__name {
    font-family: "Roboto Condensed", sans-serif; font-weight: 700;
    font-size: 21px; color: var(--brand-brown); letter-spacing: .3px; line-height: 1;
  }
  .brand__tagline {
    position: absolute; top: 65px; left: 0; white-space: nowrap;
    font-family: "Roboto Condensed", sans-serif; font-weight: 700;
    font-size: 10.5px; color: #3a3a3a; letter-spacing: .1px;
  }
  .person__name {
    position: absolute; top: 97px; left: 0;
    font-family: "Roboto Condensed", sans-serif; font-weight: 700;
    font-size: 21px; color: var(--olive); line-height: 1.1;
  }
  .person__role {
    position: absolute; top: 121px; left: 0;
    font-family: "Roboto Condensed", sans-serif; font-size: 15px;
    color: var(--title-brown);
  }
  .contact {
    position: absolute; top: 150px; left: 0; list-style: none;
    font-size: 14px; line-height: 18px;
  }
  .contact li { display: flex; align-items: center; gap: 7px; }
  .contact svg { width: 13px; height: 13px; fill: var(--icon-olive); flex: none; }
  .services__title {
    position: absolute; top: 215px; left: 0;
    font-family: "Roboto Condensed", sans-serif; font-weight: 700;
    font-size: 18px; color: var(--olive);
  }
  .services {
    position: absolute; top: 235px; left: 0; list-style: none;
    font-size: 14px; line-height: 18px;
  }
  .services li::before, .services .dot {
    content: ""; display: inline-block; width: 5px; height: 5px; border-radius: 50%;
    background: var(--olive); vertical-align: middle; margin: 0 7px 3px 0;
  }
  .services .dot { margin: 0 4px 3px 4px; }
  .photo { position: absolute; left: 342px; width: 258px; }
  .photo--dozer {
    top: 0; height: 152px;
    background: linear-gradient(180deg, var(--photo-dozer-top), var(--photo-dozer-bottom));
  }
  .photo--tractor {
    top: 155px; height: 188px;
    background: linear-gradient(180deg, var(--photo-tractor-top), var(--photo-tractor-bottom));
  }
</style>
</head>
<body>
  <div class="card">
    <div class="card__edge"></div>
    <div class="card__info">
      <div class="brand">
        <span class="brand__square"></span>
        <span class="brand__name">K &amp; R ACRE WORKS</span>
      </div>
      <div class="brand__tagline">FOR ALL OF YOUR LAND IMPROVEMENT NEEDS</div>

      <div class="person__name">WADE COLTON</div>
      <div class="person__role">OWNER</div>

      <ul class="contact">
        <li>
          <svg viewBox="0 0 16 16" aria-hidden="true"><path d="M3.6 1.2l2.3 2.7-1.3 1.8c.9 2.2 2.6 3.9 4.8 4.8l1.8-1.3 2.7 2.3-1.4 2.3C7.2 14.3 1.7 8.8 1.3 2.6z"/></svg>
          601-472-3358
        </li>
        <li>
          <svg viewBox="0 0 16 16" aria-hidden="true"><path d="M1 3h14v10H1z" /><path d="M1.5 3.5L8 8.5l6.5-5" fill="none" stroke="#f2f2f0" stroke-width="1.4"/></svg>
          wcr4817@fieldmail-example.com
        </li>
        <li>
          <svg viewBox="0 0 16 16" aria-hidden="true"><circle cx="8" cy="8" r="7"/><path d="M1.5 8h13M8 1c-2.5 3-2.5 11 0 14M8 1c2.5 3 2.5 11 0 14" fill="none" stroke="#f2f2f0" stroke-width="1.1"/></svg>
          kracreworks-example.com
        </li>
      </ul>

      <div class="services__title">WE CREADED</div>
      <ul class="services">
        <li>Land Clearing</li>
        <li>Wildlife food plots</li>
        <li>Bush Hogging</li>
        <li>Disking<span class="dot"></span>Site prep</li>
      </ul>
    </div>

    <div class="photo photo--dozer" role="img" aria-label="Photo of a yellow bulldozer pushing soil on a cleared lot"></div>
    <div class="photo photo--tractor" role="img" aria-label="Photo of an orange tractor with front loader in a grassy field"></div>
  </div>
</body>
</html>
```